9x12 Business Brochure, 3 fold, for Internet Marketing Company

I'd like to have a brochure designed for my Internet marketing company. I have the content all ready, 10 Internet Marketing Myths, which you can see here: http://www.brisklanternstudio.example/usual-web-promotion-fables/. I'm looking for something creative and business to business. The company is all about Internet marketing. I like the "http://" header I use at our website. People like it too and identify with it. Audience is business owners 35 to 55 years old. I use blue at my website. I *think* I would like the cover page (front page) to open with some attention grabbing text, that basically takes most of the front page of the brochure. It would probably say: "I Can Help You Get BETTER RESULTS from Your Website, More Traffic, TOP RANKINGS at Quorble, More Leads and MORE SALES. But first you'll have to avoid these common Internet marketing myths..." The inside pages would have the content from above (the 10 myths). The back page would have testimonials that I can provide. And the inside folded in page (or what I call the inside folded in page) would have a list of services. I think I want the dimensions 12x9 which is a larger sized, three-fold brochure.

Target Market(s)

I use this brochure to send to business owners and managers to show them I know what I'm talking about and and expert. See attachment for content.

Industry/Entity Type

Marketing

Requirements
Should not have
• No clipart. Probably not illustrations. Photos. The "http://" used at the site is something people "connect" with and get that this is about Internet marketing.

```html
<!DOCTYPE html>
<html lang="en">
<head>
<meta charset="utf-8">
<title>Practical Online Marketing – Brochure</title>
<link rel="stylesheet" href="https://fonts.googleapis.com/css2?family=Arimo:ital,wght@0,400;0,700;1,400&display=swap">
<style>
  :root{
    --navy-deep:#0a1745;
    --navy:#13275f;
    --navy-mid:#1d3f86;
    --band:#0f2456;
    --band-light:#1b3a7a;
    --ink:#1a1a1a;
    --body-grey:#555a63;
    --story-blue:#1f4f8f;
    --cyan:#6fd3ef;
    --ice:#a7e6f6;
    --white:#ffffff;
    --quote:#e3e9f7;
    --black:#050608;
    --page:#e9e9e9;
  }
  *{box-sizing:border-box;margin:0;padding:0}
  html,body{width:1200px;height:901px;overflow:hidden;background:var(--page)}
  body{font-family:"Arimo",Arial,sans-serif}
  .brochure{display:flex;width:1200px;height:901px;position:relative}
  .panel{width:400px;height:901px;position:relative;overflow:hidden}

  /* footer band across panels */
  .band{position:absolute;left:0;right:0;bottom:0;height:93px;
    background:linear-gradient(90deg,var(--band) 0%,var(--band-light) 50%,var(--band) 100%);
    color:var(--white);display:flex;flex-direction:column;justify-content:center;align-items:center;text-align:center}

  /* services panel */
  .services{background:radial-gradient(ellipse at 55% 35%,var(--navy-mid) 0%,var(--navy) 45%,var(--navy-deep) 100%);color:var(--white)}
  .services-title{position:absolute;left:64px;top:38px;font-size:37px;font-weight:700;line-height:1.15}
  .services-title span{display:block;padding-left:6px}
  .service-list{position:absolute;left:50px;top:144px;list-style:none}
  .service-list li{font-size:17px;line-height:30.6px;padding-left:24px;position:relative;white-space:nowrap}
  .service-list li::before{content:"";position:absolute;left:4px;top:12px;width:7px;height:7px;background:var(--white)}
  .services-quote{position:absolute;left:20px;right:20px;top:718px;font-style:italic;font-size:17px;line-height:29px;text-align:center;color:var(--quote);white-space:nowrap}
  .services .band{align-items:flex-start;padding-left:42px}
  .call{font-size:22px;font-weight:700}

  /* stories panel */
  .stories{background:var(--white);color:var(--ink)}
  .stories-art{position:absolute;left:48px;top:12px;width:320px;height:150px;
    background:linear-gradient(90deg,#1c4f8c 0%,#6fa8dc 45%,#dfeaf5 75%,#ffffff 100%);border-radius:6px}
  .stories-title{position:absolute;left:0;right:0;top:176px;text-align:center;font-size:40px;font-weight:700;color:var(--ink)}
  .story-list{position:absolute;left:32px;right:22px;top:242px}
  .story{font-size:13.4px;line-height:18px;color:var(--body-grey);text-align:justify;margin-bottom:22px}
  .story strong{color:var(--story-blue);font-size:17px}
  .stories .band{font-weight:700;font-size:18px;line-height:24px}

  /* cover panel */
  .cover{background:var(--black);color:var(--white)}
  .cover-art{position:absolute;left:0;top:0;width:400px;height:302px;
    background:radial-gradient(ellipse at 50% 55%,#1e4d83 0%,#0c2340 55%,#030812 100%)}
  .cover-title{position:absolute;left:0;right:0;top:30px;text-align:center;color:var(--ice);font-weight:700;line-height:.95;letter-spacing:-1px}
  .cover-title .t1{display:block;font-size:46px}
  .cover-title .t2{display:block;font-size:88px}
  .cover-title .t3{display:block;font-size:62px}
  .cover-bar{position:absolute;left:0;top:302px;width:400px;height:108px;
    background:linear-gradient(180deg,#4e7fcf 0%,#e7eef9 45%,#c9d7ef 60%,#2b58a6 100%)}
  .pitch{position:absolute;left:0;right:0;top:488px;text-align:center;font-weight:700;line-height:1.16}
  .pitch .c{color:var(--cyan);font-size:23px}
  .pitch .w{color:var(--white);font-size:32px}
  .pitch-lead{position:absolute;left:0;right:0;top:720px;text-align:center;font-size:19px;line-height:24px;color:var(--white)}
  .cover .band{font-size:18px;line-height:30px}
  .cover .band .call{font-size:26px}
</style>
</head>
<body>
<main class="brochure">

  <section class="panel services">
    <h2 class="services-title">Services &amp;<span>Expertise</span></h2>
    <ul class="service-list">
      <li>Internet Strategy Development</li>
      <li>Custom Website Design</li>
      <li>Blog Design &amp; Support</li>
      <li>Online Marketing Copywriting</li>
      <li>Social Media Marketing</li>
      <li>Search Engine Optimization (SEO)</li>
      <li>Conversion Optimization</li>
      <li>Content Marketing Management</li>
      <li>Using Friendbook for Business</li>
      <li>Quorble+, Vidstream, Pinboardly</li>
      <li>Email Marketing &amp; Production</li>
      <li>Inquiry and Lead Development</li>
      <li>Quorble AdBids Pay-Per-Click</li>
      <li>Quorble Local Places (maps)</li>
      <li>E-Commerce Development</li>
      <li>High-Performance Hosting</li>
      <li>Security &amp; Contingency Planning</li>
      <li>One-on-One or Group Training</li>
    </ul>
    <p class="services-quote">“If you think it’s expensive to hire an<br>expert, &nbsp;wait until you hire an amateur.”</p>
    <footer class="band"><p class="call">Call Us: (866) 555-0148</p></footer>
  </section>

  <section class="panel stories">
    <div class="stories-art" role="img" aria-label="Illustration of a blue globe with a circling arrow beside an http:// address bar and a pointer cursor"></div>
    <h2 class="stories-title">Success Stories</h2>
    <div class="story-list">
      <p class="story"><strong>Quorble Rankings</strong> – “... we have spent over a year trying to get onto page one at Quorble. I has been very frustrating and we’ve wasted a lot of time and money. Dana explained everything very clearly and we did everything he told us. 90 days later we’re now showing up on the first page of Quorble!</p>
      <p class="story"><strong>Website Design</strong> – “We needed a new website that properly reflected our company and the products and services we sell. We started getting more leads within 72 hours of launching the new site Dana and his team designed for us. We’re also getting better results from our Quorble AdBids pay-per-click advertising and more of those clicks are turning into inquiries!”</p>
      <p class="story"><strong>More to Come</strong> - Lorem ipsum dolor sit amet, consectetur adipiscing elit. Suspendisse justo velit, auctor ut pulvinar a, egestas non urna. Suspendisse potenti. Sed at pellentesque dolor. Vivamus sed nibh nisl. Nunc tortor tellus, facilisis eget pretium vitae, porttitor quis libero.</p>
      <p class="story"><strong>More to Come</strong> - Lorem ipsum dolor sit amet, consectetur adipiscing elit. Suspendisse justo velit, auctor ut pulvinar a, egestas non urna. Suspendisse potenti. Sed at pellentesque dolor. Vivamus sed nibh nisl. Nunc tortor tellus, facilisis eget pretium vitae, porttitor quis libero.</p>
    </div>
    <footer class="band"><p>DANA WHITLOCK<br>Dana Whitlock Consulting (.com)</p></footer>
  </section>

  <section class="panel cover">
    <div class="cover-art" role="img" aria-label="Dark blue photographic backdrop of a glowing world map made of digital code"></div>
    <h1 class="cover-title"><span class="t1">PRACTICAL</span><span class="t2">Online</span><span class="t3">Marketing</span></h1>
    <div class="cover-bar" role="img" aria-label="Close-up photo of a browser address bar reading http://www with a pointer cursor"></div>
    <p class="pitch">
      <span class="c">I Can Help You Get</span><br>
      <span class="w">BETTER RESULTS</span><br>
      <span class="c">from Your Website,</span><br>
      <span class="c">More Traffic,</span><br>
      <span class="w">TOP RANKINGS</span> <span class="c">with</span><br>
      <span class="c">Quorble, More Inquiries, &amp;</span><br>
      <span class="w">MORE SALES</span>
    </p>
    <p class="pitch-lead">But first you’ll need to avoid these<br>Common Internet Marketing Myths…</p>
    <footer class="band"><p>Dana Whitlock Consulting (.com)</p><p class="call">(866) 555-0148</p></footer>
  </section>

</main>
</body>
</html>
```